3 back Windows only wrapped for world’s smallest cargo van – midget -purple

Needed to update and clarify the description.
*Seeking award-winning graphic designer with expertise in vintage typography and vehicle branding*

**Project Overview**
Design a cohesive, high-impact vinyl wrap series for the three rear windows of a cargo van (passenger, driver, and rear). The design must convey **vintage elegance with a bold personality**, blending classical aesthetics feel with modern creative artistry. This is not a full vehicle wrap—only the three rear windows will be wrapped.

**Key Requirements**
- Three separate but visually unified designs, one for each window:
- Passenger window: 32" x 21"
- Driver window: 32.5" x 21.25"
- Rear window: 39.5" x 17.75"
- The **logo (provided)** must appear in **each window**, centrally or compositionally anchored.
- The **law firm name** must appear in **each window**, but **not necessarily adjacent to the logo**—placement should serve the overall design.
- The **phone number (555) 417-2968** must be clearly visible and included on **all three windows**.

**Design Direction**
- **Style**: Vintage with a bold personality. Think *classic hand-crafted signwriting*—inspired by **hand-lettered serifs and brush scripts**, but not imitative.
- **Tone**: Professional, authoritative, and distinctive. The vehicle should command attention as a mobile representation of elevated justice.
- **Creative Concept**: Incorporate a stylized, proprietary interpretation of **Lady Justice**, reimagined with **one hand raised higher than the other**, symbolizing that clients receive *higher justice*. This element should be subtle, artistic, and integrated into the background or border—**not literal or cliché**.
- **No traditional legal symbols** (e.g., scales, gavels, pillars) beyond those in the provided assets.
- **Color Palette**: Derived from the brand’s existing logo and reference images (designer to extract and harmonize). Must feel rich, timeless, and legible.
- **Typography**:
- Use the **existing font for the law office name** (from the logo) as a base.
- All other typography (phone, decorative text, etc.) may be experimental—**hand-drawn, brush script, or vintage serif styles encouraged**.

Target Market(s)

Consumers

Industry/Entity Type

Personal injury, law firm

Requirements
Must have
• The logo, company name, phone number, artistic input, BE CREATIVE!
Nice to have
• Nice to have one of these slogans: 1) Holding insurance companies accountable, When they refuse to be responsible. OR 2) The devil has its advocate. Justice has its Lady. The Bramwell Ward.
Should not have
• The look of a business card. BORING

```html
<!DOCTYPE html>
<html lang="en">
<head>
<meta charset="utf-8">
<title>Ivren Law – Rear Window Graphics</title>
<link rel="stylesheet" href="https://fonts.googleapis.com/css2?family=Cinzel:wght@400;600&family=Cormorant+Garamond:wght@700&family=Josefin+Sans:wght@400&display=swap">
<style>
  :root {
    --canvas: #ffffff;
    --panel: #21120f;
    --copper: #c98468;
    --copper-light: #f0bea5;
    --copper-deep: #a9614a;
    --scene-sky: #9fb6cc;
    --scene-body: #7f72b4;
  }
  * { margin: 0; padding: 0; box-sizing: border-box; }
  html, body { width: 996px; height: 1200px; overflow: hidden; background: var(--canvas); }
  .canvas { position: relative; width: 996px; height: 1200px; }
  .window-panel { position: absolute; display: block; }
  .panel-passenger { left: 28px; top: 54px; width: 450px; height: 295px; }
  .panel-driver { left: 506px; top: 51px; width: 457px; height: 298px; }
  .panel-rear { left: 213px; top: 380px; width: 555px; height: 249px; }
  .panel-bg { fill: var(--panel); }
  .frame-line { fill: none; stroke: var(--copper); stroke-width: 2; }
  .frame-dot { fill: var(--copper); }
  .firm-name { font-family: "Cinzel", serif; font-weight: 400; }
  .firm-tagline { font-family: "Josefin Sans", sans-serif; }
  .firm-motto { font-family: "Cinzel", serif; font-weight: 600; }
  .phone-number { font-family: "Cormorant Garamond", serif; font-weight: 700; }
  .phone-icon { fill: var(--copper-deep); }
  .mark-circle { fill: none; stroke: var(--copper); stroke-width: 6; }
  .vehicle-photo { position: absolute; top: 691px; height: 509px; }
  .photo-side { left: 0; width: 431px; background: linear-gradient(180deg, var(--scene-sky) 0%, var(--scene-body) 35%, var(--scene-body) 80%, #b5b0a8 100%); }
  .photo-rear { left: 431px; width: 565px; background: linear-gradient(180deg, #d9d6d0 0%, var(--scene-body) 30%, var(--scene-body) 85%, #c2bdb4 100%); }
</style>
</head>
<body>
<div class="canvas">

  <svg class="window-panel panel-passenger" viewBox="0 0 787 515" preserveAspectRatio="none" role="img" aria-label="Passenger window graphic">
    <defs>
      <linearGradient id="copperFill" x1="0" y1="0" x2="0" y2="1">
        <stop offset="0" stop-color="var(--copper-light)"/>
        <stop offset="1" stop-color="var(--copper-deep)"/>
      </linearGradient>
      <path id="handset" d="M6.62 10.79c1.44 2.83 3.76 5.14 6.59 6.59l2.2-2.2c.27-.27.67-.36 1.02-.24 1.12.37 2.33.57 3.57.57.55 0 1 .45 1 1V20c0 .55-.45 1-1 1-9.39 0-17-7.61-17-17 0-.55.45-1 1-1h3.5c.55 0 1 .45 1 1 0 1.25.2 2.45.57 3.57.11.35.03.74-.25 1.02l-2.2 2.2z"/>
    </defs>
    <rect class="panel-bg" width="787" height="515"/>
    <polygon class="frame-line" points="110,24 677,24 767,114 767,406 677,496 110,496 20,406 20,114"/>
    <rect class="frame-line" x="32" y="36" width="723" height="448" stroke-width="1.5"/>
    <g class="frame-dot"><circle cx="52" cy="54" r="2"/><circle cx="52" cy="64" r="2"/><circle cx="735" cy="54" r="2"/><circle cx="735" cy="64" r="2"/><circle cx="52" cy="456" r="2"/><circle cx="52" cy="466" r="2"/><circle cx="735" cy="456" r="2"/><circle cx="735" cy="466" r="2"/></g>
    <text class="firm-name" x="99" y="220" font-size="60" textLength="319" lengthAdjust="spacingAndGlyphs" fill="url(#copperFill)">IVREN LAW</text>
    <text class="firm-tagline" x="144" y="240" font-size="14" textLength="226" lengthAdjust="spacingAndGlyphs" fill="var(--copper)">PERSONAL INJURY LAW FIRM</text>
    <line x1="92" y1="245" x2="428" y2="245" stroke="var(--copper-light)" stroke-width="1"/>
    <text class="firm-motto" x="93" y="297" font-size="38" textLength="331" lengthAdjust="spacingAndGlyphs" fill="url(#copperFill)">The Bramwell Ward</text>
    <circle class="mark-circle" cx="594" cy="232" r="95"/>
    <use href="#handset" class="phone-icon" transform="translate(112 373.6) scale(3 3.8)"/>
    <text class="phone-number" x="191" y="447" font-size="74" textLength="437" lengthAdjust="spacingAndGlyphs" fill="url(#copperFill)">(555) 417-2968</text>
  </svg>

  <svg class="window-panel panel-driver" viewBox="0 0 800 521" preserveAspectRatio="none" role="img" aria-label="Driver window graphic">
    <rect class="panel-bg" width="800" height="521"/>
    <polygon class="frame-line" points="115,26 686,26 775,116 775,406 686,496 115,496 27,406 27,116"/>
    <rect class="frame-line" x="39" y="38" width="723" height="458" stroke-width="1.5"/>
    <g class="frame-dot"><circle cx="59" cy="54" r="2"/><circle cx="59" cy="64" r="2"/><circle cx="742" cy="54" r="2"/><circle cx="742" cy="64" r="2"/><circle cx="59" cy="456" r="2"/><circle cx="59" cy="466" r="2"/><circle cx="742" cy="456" r="2"/><circle cx="742" cy="466" r="2"/></g>
    <text class="firm-name" x="106" y="220" font-size="60" textLength="318" lengthAdjust="spacingAndGlyphs" fill="url(#copperFill)">IVREN LAW</text>
    <text class="firm-tagline" x="151" y="242" font-size="14" textLength="225" lengthAdjust="spacingAndGlyphs" fill="var(--copper)">PERSONAL INJURY LAW FIRM</text>
    <line x1="98" y1="247" x2="435" y2="247" stroke="var(--copper-light)" stroke-width="1"/>
    <text class="firm-motto" x="93" y="297" font-size="38" textLength="330" lengthAdjust="spacingAndGlyphs" fill="url(#copperFill)">The Bramwell Ward</text>
    <circle class="mark-circle" cx="588" cy="236" r="95"/>
    <use href="#handset" class="phone-icon" transform="translate(118 373.6) scale(3 3.8)"/>
    <text class="phone-number" x="197" y="447" font-size="74" textLength="438" lengthAdjust="spacingAndGlyphs" fill="url(#copperFill)">(555) 417-2968</text>
  </svg>

  <svg class="window-panel panel-rear" viewBox="0 0 971 435" preserveAspectRatio="none" role="img" aria-label="Rear window graphic">
    <rect class="panel-bg" width="971" height="435"/>
    <polygon class="frame-line" points="95,17 877,17 952,92 952,330 877,405 95,405 18,330 18,92"/>
    <rect class="frame-line" x="30" y="28" width="911" height="378" stroke-width="1.5"/>
    <g class="frame-dot"><circle cx="46" cy="40" r="2"/><circle cx="46" cy="50" r="2"/><circle cx="926" cy="40" r="2"/><circle cx="926" cy="50" r="2"/><circle cx="46" cy="380" r="2"/><circle cx="46" cy="390" r="2"/><circle cx="926" cy="380" r="2"/><circle cx="926" cy="390" r="2"/></g>
    <text class="firm-name" x="123" y="236" font-size="88" textLength="202" lengthAdjust="spacingAndGlyphs" fill="url(#copperFill)">IVREN</text>
    <text class="firm-name" x="658" y="236" font-size="88" textLength="205" lengthAdjust="spacingAndGlyphs" fill="url(#copperFill)">LAW</text>
    <circle class="mark-circle" cx="487" cy="185" r="100"/>
    <use href="#handset" class="phone-icon" transform="translate(230.4 298.7) scale(3.2 4.1)"/>
    <text class="phone-number" x="308" y="368" font-size="72" textLength="433" lengthAdjust="spacingAndGlyphs" fill="url(#copperFill)">(555) 417-2968</text>
  </svg>

  <div class="vehicle-photo photo-side" role="img" aria-label="Photo of the purple mini cargo van from the side with the window graphic applied"></div>
  <div class="vehicle-photo photo-rear" role="img" aria-label="Photo of the purple mini cargo van from behind with the rear window graphic applied"></div>

</div>
</body>
</html>
```